TK Homes - Stone Dorf Design

Looking for a double sides design, 1 side for my realestate and the other for home building. ( TK Homes on 1 side, Stone Dorf card on the other Side
Side 1 - Marek Tove ~ Vox Realty logo and Company ( the Property quarter )
Marek Tove
Marek@Marektove.example
IG - Marek_Bzq_Realtor
FB - marekt
Cell - 5558130467
3847 61 St Nw

Side 2
Marek Tove
5558130467
IG - Stonedorf_Bzq
Stonedorfdev@mailbox.example

Target Market(s)

Home buyers/ sellers

Industry/Entity Type

Home builders - Realestate

Contact Information for Business Card

Above

Requirements
Must have
• Black OR White background - my information -

```html
<!DOCTYPE html>
<html lang="en">
<head>
<meta charset="utf-8">
<title>Marek Tove – Business Cards</title>
<link rel="stylesheet" href="https://fonts.googleapis.com/css2?family=Cinzel:wght@600&family=Tinos:wght@400;700&display=swap">
<style>
  :root {
    --bg: #2b2c31;
    --card: #1d1e23;
    --blue: #1573c4;
    --gold: #f3c233;
    --white: #f2f2f2;
  }
  * { margin: 0; padding: 0; box-sizing: border-box; }
  html, body { width: 1200px; height: 780px; overflow: hidden; background: var(--bg); }
  .canvas { position: relative; width: 1200px; height: 780px; }

  .card {
    position: absolute; left: 290px; width: 620px; height: 354px;
    background: var(--card); border-radius: 22px;
    border: 3px solid var(--gold); overflow: hidden;
    font-family: "Tinos", "Times New Roman", serif; color: var(--white);
  }
  .card--builder { top: 24px; }
  .card--realty { top: 402px; }

  .name-tab { position: absolute; top: 0; right: 0; width: 220px; height: 92px; }
  .name-tab__band { position: absolute; top: 0; right: 34px; width: 20px; height: 40px; background: var(--blue); }
  .name-tab__name { position: absolute; top: 18px; right: 62px; font-weight: 700; font-size: 27px; white-space: nowrap; }
  .name-tab__first { color: var(--blue); }
  .name-tab__last { color: var(--gold); }
  .name-tab__role { position: absolute; top: 52px; right: 62px; font-weight: 700; font-size: 15px; color: var(--white); }

  .contact-list { position: absolute; left: 44px; bottom: 34px; list-style: none; }
  .contact-list li { display: flex; align-items: center; gap: 10px; font-size: 16px; line-height: 22px; }
  .contact-icon { width: 14px; height: 14px; flex: none; }
  .contact-dot { width: 13px; height: 13px; flex: none; background: var(--blue); border-radius: 50%; }
  .contact-square { width: 13px; height: 13px; flex: none; border: 2px solid var(--blue); border-radius: 3px; }

  .company-name {
    position: absolute; left: 44px; top: 120px;
    font-weight: 700; font-size: 40px; line-height: 44px;
    color: var(--blue); letter-spacing: 1px;
  }
  .company-name span { display: block; font-size: 22px; letter-spacing: 6px; }

  .brand-mark {
    position: absolute; left: 44px; top: 52px;
    font-weight: 700; font-size: 34px; color: var(--blue);
  }
  .agent-name {
    position: absolute; left: 44px; top: 104px;
    font-family: "Cinzel", "Times New Roman", serif; font-weight: 600;
    font-size: 40px; letter-spacing: 2px; white-space: nowrap;
  }
  .agent-name__first { color: var(--blue); }
  .agent-name__last { color: var(--gold); }
  .address { position: absolute; right: 40px; bottom: 40px; font-size: 17px; }
</style>
</head>
<body>
<div class="canvas">

  <section class="card card--builder">
    <div class="company-name">Stone Dorf<span>Developments</span></div>

    <div class="name-tab">
      <div class="name-tab__band"></div>
      <div class="name-tab__name"><span class="name-tab__first">Marek</span> <span class="name-tab__last">Tove</span></div>
      <div class="name-tab__role">Director</div>
    </div>

    <ul class="contact-list">
      <li><svg class="contact-icon" viewBox="0 0 24 24"><path fill="#1573c4" d="M6.6 10.8a15 15 0 0 0 6.6 6.6l2.2-2.2a1 1 0 0 1 1-.25 11.4 11.4 0 0 0 3.6.6 1 1 0 0 1 1 1V20a1 1 0 0 1-1 1A17 17 0 0 1 3 4a1 1 0 0 1 1-1h3.5a1 1 0 0 1 1 1c0 1.25.2 2.45.6 3.6a1 1 0 0 1-.25 1z"/></svg>5558130467</li>
      <li><span class="contact-square"></span>Stonedorf_Bzq</li>
      <li><svg class="contact-icon" viewBox="0 0 24 24"><path fill="#1573c4" d="M2 5h20v14H2z"/><path fill="none" stroke="#1d1e23" stroke-width="2" d="M2 5l10 8 10-8"/></svg>Stonedorfdev@mailbox.example</li>
    </ul>
  </section>

  <section class="card card--realty">
    <div class="brand-mark">TK Homes</div>
    <div class="agent-name"><span class="agent-name__first">Marek</span> <span class="agent-name__last">Tove</span></div>

    <div class="name-tab">
      <div class="name-tab__band"></div>
      <div class="name-tab__name"><span class="name-tab__first">Marek</span> <span class="name-tab__last">Tove</span></div>
      <div class="name-tab__role">Director</div>
    </div>

    <ul class="contact-list">
      <li><svg class="contact-icon" viewBox="0 0 24 24"><path fill="#1573c4" d="M6.6 10.8a15 15 0 0 0 6.6 6.6l2.2-2.2a1 1 0 0 1 1-.25 11.4 11.4 0 0 0 3.6.6 1 1 0 0 1 1 1V20a1 1 0 0 1-1 1A17 17 0 0 1 3 4a1 1 0 0 1 1-1h3.5a1 1 0 0 1 1 1c0 1.25.2 2.45.6 3.6a1 1 0 0 1-.25 1z"/></svg>5558130467</li>
      <li><span class="contact-dot"></span>marekt</li>
      <li><span class="contact-square"></span>Marek_Bzq_Realtor</li>
      <li><svg class="contact-icon" viewBox="0 0 24 24"><path fill="#1573c4" d="M2 5h20v14H2z"/><path fill="none" stroke="#1d1e23" stroke-width="2" d="M2 5l10 8 10-8"/></svg>Marek@Marektove.example</li>
      <li><svg class="contact-icon" viewBox="0 0 24 24"><g fill="none" stroke="#1573c4" stroke-width="2"><circle cx="12" cy="12" r="10"/><ellipse cx="12" cy="12" rx="4" ry="10"/><path d="M2 12h20"/></g></svg>www.marektove.example</li>
    </ul>

    <div class="address">3847 61 St Nw</div>
  </section>

</div>
</body>
</html>
```